Design a New Business Card for Our Company

We are looking for fresh, unique, and a modern business card that reflects our roots as digital marketing agency focused on SEM.

Industry/Entity Type

Marketing

Contact Information for Business Card

looking for very unique out of the box designs. clean and modern that compliments our logo

Requirements
Must have
• colors should match our logo
• Front should have name, address, email, and phone/fax of the person, phone/fax are the same number
• back should have our url

```html
<!DOCTYPE html>
<html lang="en">
<head>
<meta charset="utf-8">
<title>Keystep Business Card</title>
<link href="https://fonts.googleapis.com/css2?family=Roboto:wght@400;500;700&display=swap" rel="stylesheet">
<style>
  :root {
    --backdrop: #4a3f38;
    --card: #151515;
    --card-edge: #222222;
    --ink: #e6e6e6;
    --ink-soft: #b9b9b9;
    --accent: #4a90d9;
    --rule: #6a6a6a;
  }
  * { box-sizing: border-box; margin: 0; padding: 0; }
  html, body {
    width: 1200px; height: 787px; overflow: hidden;
    background: var(--backdrop);
    font-family: "Roboto", Arial, sans-serif;
  }
  .sheet {
    position: relative; width: 1200px; height: 787px;
    display: flex; align-items: center; justify-content: center; gap: 40px;
  }
  .card {
    position: relative; width: 540px; height: 309px;
    background: var(--card);
    border: 1px solid var(--card-edge);
    border-radius: 4px;
    box-shadow: 0 14px 30px rgba(0,0,0,0.45);
    overflow: hidden;
  }
  /* back */
  .card-back .brand-mark {
    position: absolute; left: 150px; top: 86px;
    display: flex; align-items: center; gap: 14px;
  }
  .card-back .brand-dot {
    width: 40px; height: 40px; border-radius: 50%;
    background: var(--ink-soft);
  }
  .card-back .brand-name {
    font-weight: 700; font-size: 44px; color: var(--ink-soft);
    letter-spacing: -0.5px;
  }
  .card-back .website {
    position: absolute; left: 44px; bottom: 74px;
    font-size: 13px; letter-spacing: 5px; color: var(--ink);
  }
  /* front */
  .card-front .brand-mark {
    position: absolute; left: 196px; top: 74px;
    display: flex; align-items: center; gap: 12px;
  }
  .card-front .brand-dot {
    width: 30px; height: 30px; border-radius: 50%;
    background: var(--accent);
  }
  .card-front .brand-name {
    font-weight: 700; font-size: 46px; color: var(--ink);
    letter-spacing: -0.5px;
  }
  .holder {
    position: absolute; right: 318px; top: 176px; text-align: right;
  }
  .holder-name { font-size: 18px; font-weight: 500; color: var(--ink-soft); }
  .holder-title { font-size: 15px; color: var(--accent); margin-top: 2px; }
  .divider {
    position: absolute; left: 240px; top: 166px;
    width: 1px; height: 110px; background: var(--rule);
  }
  .contact {
    position: absolute; left: 258px; top: 168px;
    list-style: none; color: var(--ink); font-size: 15px; line-height: 20px;
  }
  .contact li { display: flex; align-items: center; gap: 8px; }
  .contact .address { margin-bottom: 4px; }
  .contact .icon { width: 14px; height: 14px; fill: var(--ink-soft); flex: none; }
</style>
</head>
<body>
<main class="sheet">
  <section class="card card-back" aria-label="Card back">
    <div class="brand-mark">
      <span class="brand-dot"></span>
      <span class="brand-name">Keystep</span>
    </div>
    <p class="website">www.keystepmedia.com</p>
  </section>

  <section class="card card-front" aria-label="Card front">
    <div class="brand-mark">
      <span class="brand-dot"></span>
      <span class="brand-name">Keystep</span>
    </div>

    <div class="holder">
      <p class="holder-name">Alan Brooke</p>
      <p class="holder-title">President</p>
    </div>

    <span class="divider"></span>

    <ul class="contact">
      <li class="address">2190 Linden Avenue<br>Maple Grove, NY 11402</li>
      <li>
        <svg class="icon" viewBox="0 0 16 16" aria-hidden="true"><path d="M3 2h3l1.5 3.5L5.5 7a8 8 0 0 0 3.5 3.5l1.5-2L14 10v3a1 1 0 0 1-1 1A11 11 0 0 1 2 3a1 1 0 0 1 1-1z"/></svg>
        555 0142 7781
      </li>
      <li>
        <svg class="icon" viewBox="0 0 16 16" aria-hidden="true"><path d="M4 1h8v4H4zM2 6h12a1 1 0 0 1 1 1v5h-3v3H4v-3H1V7a1 1 0 0 1 1-1zm3 6v2h6v-2z"/></svg>
        555 0193 4620
      </li>
      <li>
        <svg class="icon" viewBox="0 0 16 16" aria-hidden="true"><path d="M1 3h14v10H1zm1.5 1.2V5l5.5 4 5.5-4v-.8z"/></svg>
        alan@keystepmedia.com
      </li>
    </ul>
  </section>
</main>
</body>
</html>
```